CoinHarbor.com Site Redesign

We are looking to redesign our CoinHarbor.com site. This site is focused on helping consumers make smart financial decisions. We provide reviews and articles in various categories.

We are looking for a responsive design to run on wordpress. We will also have adsense advertisements on our page and will want some ad spot space. We are thinking of two column design vs. single column.

Here is an example of what our competitors look like:
ShopperBeacon.org (mostly reviews vs. articles)
Homepage - https://www.shopperbeacon.example/
Category Review Listing - https://www.shopperbeacon.example/mortgage-refinance/best-mortgage-refinance
Individual Review - https://www.shopperbeacon.example/mortgage-refinance/c/loan-orchard-mortgage-refinance-review

- I like that the site is extremely clean. I like the fixed header in mobile

PilotGuide
Homepage - https://www.pilotguide.example/
Category Review Listing-https://www.pilotguide.example/auto_insurance/index.php
Individual Review- https://www.pilotguide.example/auto_insurance/drivora_review.php

Articles - https://www.pilotguide.example/blog/2017/11/20/going-on-a-holiday-road-trip-be-prepared-for-these-hazards/

What I Like? I like the two column layout in that it gives room for advertising.
What I Do NOT Like? The top navigation is a little cumbersome and old. Mobile view is not very good. Content seems a bit cluttered.

PennyMoth
Homepage - https://www.pennymoth.example
Category Review Listing - https://www.pennymoth.example/blog/insurance/best-car-insurance-companies/?trk=pm_gn1_4.0
Individual Review- https://www.pennymoth.example/blog/insurance/veloro-insurance-review/

What I Like? very clean. Like the use of white space and focus on bright color call to action buttons.
What I Do NOT Like? In mobile a lot of content is pushed below the fold because of the large image above the fold. Reviews are not well organized.

Target Market(s)

consumers interested in saving money and making smart financial decisions

Industry/Entity Type

Financial

Logo Text

CoinHarbor.com or CoinHarbor

Coding

Coded - Design and coding required

Number of Pages Required

5+ page

Font styles to use
Sans Serif

Colors

Designer to choose colors to be used in the design.

Requirements
Must have
• -responsive design
• -room for ad space in the right column
Nice to have
• -good use of white space
• -clean layouts
Should not have
• -clutter

```html
<!DOCTYPE html>
<html lang="en">
<head>
<meta charset="utf-8">
<title>CoinHarbor.com – Make Smarter Financial Decisions</title>
<link href="https://fonts.googleapis.com/css2?family=Lato:ital,wght@0,400;0,700;0,900;1,400&family=Oswald:wght@500&display=swap" rel="stylesheet">
<style>
:root{
  --blue:#0d9fd8;
  --blue-dark:#0a86b8;
  --navy:#17397a;
  --ink:#222;
  --text:#444;
  --muted:#666;
  --panel:#ebebeb;
  --slate:#4a4a4a;
  --footer:#2e2e2e;
  --white:#fff;
}
*{box-sizing:border-box;margin:0;padding:0}
html,body{width:1200px;height:2449px;overflow:hidden;background:var(--white)}
body{font-family:"Lato",sans-serif;color:var(--text);position:relative}
a{color:inherit;text-decoration:none}

/* Header */
.site-header{position:absolute;left:0;top:0;width:1200px;height:91px}
.brand{position:absolute;left:98px;top:28px;display:flex;align-items:center;gap:10px}
.brand-mark{width:30px;height:30px;background:var(--blue);display:block}
.brand-name{font-size:25px;font-weight:700;color:var(--navy)}
.tagline{position:absolute;right:100px;top:36px;font-size:17px;font-style:italic;color:var(--ink)}

.main-nav{position:absolute;left:0;top:91px;width:1200px;height:56px;background:var(--blue)}
.main-nav a{position:absolute;top:19px;font-size:15px;font-weight:700;color:var(--white);letter-spacing:.2px}

/* Hero */
.hero{position:absolute;left:0;top:147px;width:1200px;height:343px;
  background:linear-gradient(100deg,#3d4347 0%,#5a6064 35%,#4b4f52 65%,#2f2a26 100%)}
.hero-search{position:absolute;left:263px;top:67px;width:672px;height:49px;display:flex}
.hero-search .field{flex:1;background:var(--white);font-size:18px;color:#555;padding:14px 14px}
.hero-search .btn{width:126px;background:var(--navy);color:var(--white);font-weight:700;font-size:17px;
  display:flex;align-items:center;justify-content:center;border:2px solid var(--white);border-left:0}
.hero h1{position:absolute;left:0;width:1200px;top:160px;text-align:center;color:var(--white);font-size:47px;font-weight:700}
.hero p{position:absolute;left:0;width:1200px;top:240px;text-align:center;color:var(--white);font-size:22px;font-weight:700}

/* Category finder */
.finder{position:absolute;left:98px;top:567px;width:632px;height:55px;background:#ddd;padding:6px}
.finder div{background:var(--white);height:43px;font-size:17px;color:var(--ink);padding:11px 10px}
.finder span{color:#777}

.tiles{position:absolute;left:98px;top:653px;width:632px;display:grid;grid-template-columns:repeat(3,199px);grid-auto-rows:154px;gap:17px}
.tile{position:relative;display:flex;align-items:center;justify-content:center;text-align:center;
  color:var(--white);font-size:19px;font-weight:700;line-height:1.3;text-shadow:0 1px 3px rgba(0,0,0,.6)}
.tile .photo{position:absolute;inset:0}
.tile span{position:relative;padding:0 12px}

/* Sidebar */
.sidebar-title{position:absolute;left:753px;width:347px;height:55px;background:var(--navy);color:var(--white);
  font-size:21px;font-weight:700;display:flex;align-items:center;justify-content:center}
.sidebar-sub{position:absolute;left:753px;top:641px;width:347px;text-align:center;font-size:17px;color:var(--muted)}
.feature{position:absolute;left:753px;width:347px;height:113px;display:flex;align-items:center;color:var(--white)}
.feature.blue{background:var(--blue)}
.feature.dark{background:var(--slate)}
.feature .icon{width:90px;height:90px;border-radius:50%;background:var(--white);margin:0 22px 0 12px;flex:none;display:flex;align-items:center;justify-content:center}
.feature h3{font-size:18px;font-weight:700;margin-bottom:8px}
.feature p{font-size:14px;font-weight:700;line-height:1.4}

.recommended{position:absolute;left:753px;top:1154px;width:347px;height:337px;background:var(--panel);padding:22px 14px 0 14px}
.rec-item{display:flex;gap:12px;margin-bottom:18px}
.rec-thumb{width:64px;height:50px;flex:none;margin-top:4px;background:linear-gradient(135deg,#9aa7ae,#5d6d76)}
.rec-item h4{font-size:16px;font-weight:700;color:var(--ink);margin-bottom:4px}
.rec-item p{font-size:13.5px;line-height:1.45;color:var(--text);text-align:justify}

/* Recent articles */
.recent-head{position:absolute;left:98px;top:1530px;width:632px;height:55px;background:#e5e5e5;
  color:var(--blue);font-size:23px;font-weight:700;padding:13px 19px}
.article{position:absolute;width:300px;display:flex;gap:22px}
.article .num{width:37px;height:37px;background:var(--blue);color:var(--white);font-size:21px;font-weight:700;flex:none;
  display:flex;align-items:center;justify-content:center}
.article h3{font-size:16px;font-weight:700;color:var(--ink);line-height:1.3;margin-bottom:12px}
.article p{font-size:13.5px;line-height:1.55;text-align:justify;color:var(--text)}

/* Ad */
.ad{position:absolute;left:753px;top:1530px;width:347px;height:402px;background:#f3f3f3;border:1px solid #ddd;overflow:hidden}
.ad .photo{position:absolute;left:0;top:0;width:347px;height:340px;background:linear-gradient(160deg,#fafafa 0%,#e6e6e6 60%,#cfcfcf 100%)}
.ad .headline{position:absolute;right:30px;top:38px;text-align:right;font-family:"Oswald",sans-serif;font-size:22px;line-height:1.55;color:var(--blue-dark)}
.ad .learn{position:absolute;right:30px;top:188px;border:2px solid var(--blue-dark);color:var(--blue-dark);font-size:12px;font-weight:700;padding:7px 8px;background:var(--white)}
.ad .ad-brand{position:absolute;left:0;bottom:0;width:347px;height:62px;background:var(--white);display:flex;align-items:center;justify-content:center;gap:8px}
.ad .ad-brand i{width:24px;height:24px;background:var(--blue);display:block}
.ad .ad-brand b{font-size:21px;color:var(--navy)}

/* Footer */
.site-footer{position:absolute;left:0;top:2018px;width:1200px;height:431px;background:var(--footer);color:var(--white)}
.site-footer h4{position:absolute;font-size:19px;font-weight:700;line-height:1.4}
.site-footer ul{position:absolute;list-style:none;font-size:14px;color:#e6e6e6}
.site-footer li{height:25.8px;display:flex;align-items:center;gap:10px}
.site-footer li svg{flex:none}
.newsletter{position:absolute;left:793px;top:156px;display:flex;gap:10px}
.newsletter .email{width:256px;height:44px;border:2px solid var(--white);font-size:14px;padding:12px 12px}
.newsletter .go{width:42px;height:44px;background:var(--blue);border:2px solid var(--white);font-weight:700;font-size:14px;display:flex;align-items:center;justify-content:center}
.footer-rule{position:absolute;left:98px;top:348px;width:1002px;height:1px;background:#bbb}
.copyright{position:absolute;left:0;width:1200px;top:382px;text-align:center;font-size:15px;font-weight:700}
</style>
</head>
<body>

<header class="site-header">
  <a class="brand" href="#"><i class="brand-mark"></i><span class="brand-name">CoinHarbor.com</span></a>
  <p class="tagline">Trusted Financial Advice and Reviews Since 2001</p>
</header>

<nav class="main-nav">
  <a href="#" style="left:98px">HOME</a>
  <a href="#" style="left:189px">ANNUITIES</a>
  <a href="#" style="left:317px">AUTO INSURANCE</a>
  <a href="#" style="left:501px">CREDIT MONITORING</a>
  <a href="#" style="left:713px">DEBT MANAGEMENT</a>
  <a href="#" style="left:918px">MORTGAGES</a>
</nav>

<section class="hero" role="img" aria-label="Desk with a laptop, paperwork and a coffee cup behind the search area">
  <div class="hero-search"><div class="field">Custom Search</div><div class="btn">SEARCH</div></div>
  <h1>Make Smarter Financial Decisions</h1>
  <p>FIND THE BEST FINANCIAL PRODUCTS &amp; SERVICES</p>
</section>

<div class="finder"><div>I'm looking for <span>product or category</span></div></div>

<div class="tiles">
  <a class="tile" href="#"><div class="photo" role="img" aria-label="Businessman with coin imagery" style="background:linear-gradient(135deg,#2a5a86,#7a4a2a)"></div><span>Annuities</span></a>
  <a class="tile" href="#"><div class="photo" role="img" aria-label="Toy car on a blue desk" style="background:linear-gradient(135deg,#2a8fb8,#1a5f86)"></div><span>Auto Insurance</span></a>
  <a class="tile" href="#"><div class="photo" role="img" aria-label="Hands holding a wallet and cards" style="background:linear-gradient(135deg,#3a3d40,#6a6e72)"></div><span>Credit Monitoring</span></a>
  <a class="tile" href="#"><div class="photo" role="img" aria-label="Smiling woman in a bright office" style="background:linear-gradient(135deg,#3aa8d6,#1d7fae)"></div><span>Credit Repair</span></a>
  <a class="tile" href="#"><div class="photo" role="img" aria-label="Advisor working at a laptop" style="background:linear-gradient(135deg,#4a3a30,#2a2420)"></div><span>Debt Management</span></a>
  <a class="tile" href="#"><div class="photo" role="img" aria-label="Digital security lights" style="background:linear-gradient(135deg,#0e5a5a,#1a3a4a)"></div><span>Identity Theft</span></a>
  <a class="tile" href="#"><div class="photo" role="img" aria-label="Insurance papers with a chart" style="background:linear-gradient(135deg,#5a5a5a,#a08a70)"></div><span>Life Insurance</span></a>
  <a class="tile" href="#"><div class="photo" role="img" aria-label="Family reviewing mortgage documents" style="background:linear-gradient(135deg,#3c9cc8,#1e6a92)"></div><span>Mortgages</span></a>
  <a class="tile" href="#"><div class="photo" role="img" aria-label="Couple looking at a laptop" style="background:linear-gradient(135deg,#6a6460,#3a3634)"></div><span>Online Brokerages</span></a>
  <a class="tile" href="#"><div class="photo" role="img" aria-label="Mortgage application form" style="background:linear-gradient(135deg,#2f7fc0,#1a4f86)"></div><span>Payday Loans</span></a>
  <a class="tile" href="#"><div class="photo" role="img" aria-label="Couple reviewing household bills" style="background:linear-gradient(135deg,#3a3230,#6a5a50)"></div><span>Personal Finance</span></a>
  <a class="tile" href="#"><div class="photo" role="img" aria-label="Stacks of coins on a teal background" style="background:linear-gradient(135deg,#1aa0b8,#0e5a70)"></div><span>Student Loan<br>Consolidation</span></a>
  <a class="tile" href="#"><div class="photo" role="img" aria-label="Person holding their head over a small house" style="background:linear-gradient(135deg,#5a5a5a,#2a2a2a)"></div><span>Tax Settlement</span></a>
</div>

<aside>
  <div class="sidebar-title" style="top:567px">What is CoinHarbor.com?</div>
  <p class="sidebar-sub">Financial Service Advice and Reviews</p>

  <div class="feature blue" style="top:695px">
    <div class="icon"><svg width="50" height="50" viewBox="0 0 50 50"><circle cx="20" cy="20" r="12" fill="#cfe6f3" stroke="#555" stroke-width="4"/><line x1="29" y1="29" x2="42" y2="42" stroke="#333" stroke-width="7" stroke-linecap="round"/></svg></div>
    <div><h3>We Analyze &amp; Explain</h3><p>We analyze &amp; explain how each online service works</p></div>
  </div>
  <div class="feature dark" style="top:824px">
    <div class="icon"><svg width="46" height="50" viewBox="0 0 46 50"><rect x="6" y="6" width="32" height="40" fill="#f6f1dc" stroke="#777" stroke-width="2"/><rect x="15" y="2" width="14" height="8" fill="#999"/><g stroke="#4a7a3a" stroke-width="3"><line x1="12" y1="20" x2="32" y2="20"/><line x1="12" y1="28" x2="32" y2="28"/><line x1="12" y1="36" x2="26" y2="36"/></g></svg></div>
    <div><h3>We Test &amp; Compare</h3><p>We test &amp; compare the leading services in each category</p></div>
  </div>
  <div class="feature blue" style="top:953px">
    <div class="icon"><svg width="52" height="50" viewBox="0 0 52 50"><polygon points="26,2 32,19 50,19 36,30 41,48 26,37 11,48 16,30 2,19 20,19" fill="#f2a81d" stroke="#c27a10" stroke-width="1.5"/></svg></div>
    <div><h3>We Review &amp; Rate</h3><p>We review and rate each service to show which is best</p></div>
  </div>

  <div class="sidebar-title" style="top:1099px">Recommended Articles</div>
  <div class="recommended">
    <div class="rec-item"><div class="rec-thumb" role="img" aria-label="Calculator and papers"></div><div><h4>Annuity Factor Method Explained</h4><p>The "Annuity Factor Method" is a method to calculate the dollar amount of all eligible withdrawals.</p></div></div>
    <div class="rec-item"><div class="rec-thumb" role="img" aria-label="Hand writing with a pen"></div><div><h4>What is the Best Annuity for You?</h4><p>The simple answer is, the "best" annuity is one that serves all your retirement needs.</p></div></div>
    <div class="rec-item"><div class="rec-thumb" role="img" aria-label="Blue financial chart" style="background:linear-gradient(135deg,#2a8fc8,#bfe0f0)"></div><div><h4>Is an Annuity Right for You?</h4><p>If you are looking for a retirement product with less risk than those direct investments.</p></div></div>
  </div>
</aside>

<section>
  <h2 class="recent-head">Recent Articles</h2>
  <article class="article" style="left:98px;top:1638px"><div class="num">1</div><div><h3>5 "Easy" Ways Parents Can Save $1000's a Year</h3><p>Parents, let's face it – the high cost of raising children leaves us all needing a little extra money. Short of getting a big raise, switching jobs, or winning..</p></div></article>
  <article class="article" style="left:433px;top:1638px"><div class="num">2</div><div><h3>How Do I Get Cheap Auto Insurance?</h3><p>Parents, let's face it – the high cost of raising children leaves us all needing a little extra money. Short of getting a big raise, switching jobs, or winning..</p></div></article>
  <article class="article" style="left:98px;top:1807px"><div class="num">3</div><div><h3>How Do I Buy General Auto Insurance?</h3><p>Most people already have budgets that are extremely stretched; therefore, it is not surprising that most people want to spend the least amount.</p></div></article>
  <article class="article" style="left:433px;top:1807px"><div class="num">4</div><div><h3>How to Shop for Young Driver's Insurance?</h3><p>Everyone one needs car insurance, including young drivers...especially young drivers. Auto insurance for young drivers can often be rather.</p></div></article>
</section>

<div class="ad">
  <div class="photo" role="img" aria-label="Hand holding car keys out of a computer monitor"></div>
  <div class="headline">MAKE<br>SMARTER<br>FINANCIAL<br>DECISIONS</div>
  <div class="learn">LEARN MORE</div>
  <div class="ad-brand"><i></i><b>CoinHarbor.com</b></div>
</div>

<footer class="site-footer">
  <h4 style="left:98px;top:56px">All Services Reviewed</h4>
  <ul style="left:98px;top:126px">
    <li><svg width="12" height="10" viewBox="0 0 12 10"><path d="M1 5h9M6 1l4 4-4 4" stroke="#ddd" stroke-width="1.6" fill="none"/></svg>Annuities</li>
    <li><svg width="12" height="10" viewBox="0 0 12 10"><path d="M1 5h9M6 1l4 4-4 4" stroke="#ddd" stroke-width="1.6" fill="none"/></svg>Auto Insurance</li>
    <li><svg width="12" height="10" viewBox="0 0 12 10"><path d="M1 5h9M6 1l4 4-4 4" stroke="#ddd" stroke-width="1.6" fill="none"/></svg>Credit Monitoring</li>
    <li><svg width="12" height="10" viewBox="0 0 12 10"><path d="M1 5h9M6 1l4 4-4 4" stroke="#ddd" stroke-width="1.6" fill="none"/></svg>Credit Repair</li>
    <li><svg width="12" height="10" viewBox="0 0 12 10"><path d="M1 5h9M6 1l4 4-4 4" stroke="#ddd" stroke-width="1.6" fill="none"/></svg>Debt Management</li>
    <li><svg width="12" height="10" viewBox="0 0 12 10"><path d="M1 5h9M6 1l4 4-4 4" stroke="#ddd" stroke-width="1.6" fill="none"/></svg>Homeowners Insurance</li>
    <li><svg width="12" height="10" viewBox="0 0 12 10"><path d="M1 5h9M6 1l4 4-4 4" stroke="#ddd" stroke-width="1.6" fill="none"/></svg>Identity Theft</li>
  </ul>
  <ul style="left:310px;top:126px">
    <li><svg width="12" height="10" viewBox="0 0 12 10"><path d="M1 5h9M6 1l4 4-4 4" stroke="#ddd" stroke-width="1.6" fill="none"/></svg>Life Insurance</li>
    <li><svg width="12" height="10" viewBox="0 0 12 10"><path d="M1 5h9M6 1l4 4-4 4" stroke="#ddd" stroke-width="1.6" fill="none"/></svg>Mortgages</li>
    <li><svg width="12" height="10" viewBox="0 0 12 10"><path d="M1 5h9M6 1l4 4-4 4" stroke="#ddd" stroke-width="1.6" fill="none"/></svg>Online Brokerages</li>
    <li><svg width="12" height="10" viewBox="0 0 12 10"><path d="M1 5h9M6 1l4 4-4 4" stroke="#ddd" stroke-width="1.6" fill="none"/></svg>Payday Loans</li>
    <li><svg width="12" height="10" viewBox="0 0 12 10"><path d="M1 5h9M6 1l4 4-4 4" stroke="#ddd" stroke-width="1.6" fill="none"/></svg>Personal Finance</li>
    <li><svg width="12" height="10" viewBox="0 0 12 10"><path d="M1 5h9M6 1l4 4-4 4" stroke="#ddd" stroke-width="1.6" fill="none"/></svg>Student Loan Consolidation</li>
  </ul>
  <h4 style="left:561px;top:56px">Popular Services<br>Reviewed</h4>
  <ul style="left:561px;top:126px">
    <li><svg width="12" height="10" viewBox="0 0 12 10"><path d="M1 5h9M6 1l4 4-4 4" stroke="#ddd" stroke-width="1.6" fill="none"/></svg>Debt Management</li>
    <li><svg width="12" height="10" viewBox="0 0 12 10"><path d="M1 5h9M6 1l4 4-4 4" stroke="#ddd" stroke-width="1.6" fill="none"/></svg>Payday Loans</li>
    <li><svg width="12" height="10" viewBox="0 0 12 10"><path d="M1 5h9M6 1l4 4-4 4" stroke="#ddd" stroke-width="1.6" fill="none"/></svg>Credit Cards</li>
  </ul>
  <h4 style="left:793px;top:56px">Subscribe To Our Newsletter<br>To Get The Latest Great Deals<br>And Reviews</h4>
  <div class="newsletter"><div class="email">Enter Your Email</div><div class="go">GO</div></div>
  <div class="footer-rule"></div>
  <p class="copyright">Copyright © 2017 CoinHarbor. All rights reserved.</p>
</footer>

</body>
</html>
```